Veltrane Group Business Card Design

The CEO is looking for a new trendy look for his business card.
You can stay with current branding or come up with something new/creative. It can be 3D, including Medical Office buildings. You can use our logo in a variety of colors. Please include name, title, company name, company website, email address, cell number

Target Market(s)

Real Estate Development and Construction

Industry/Entity Type

Health care real estate

Contact Information for Business Card

Rohesh Kamdar, CEO M-604.781.2249 E-roheshkamdar@veltrane.com Address:4180 Lindqvist Ave, Tampa, FL 33482 www.veltrane.com

Font styles to use
Other font styles liked:
• Be creative

Requirements
Must have
• Creative, trendy look
Nice to have
• Please go to our website to get a feel- www. veltrane.com
Should not have
• small fonts

```html
<!DOCTYPE html>
<html lang="en">
<head>
<meta charset="utf-8">
<title>Veltrane Group Business Card</title>
<link href="https://fonts.googleapis.com/css2?family=Lato:wght@300;400;700;900&display=swap" rel="stylesheet">
<style>
  :root {
    --stage: #cfcfcf;
    --paper: #ffffff;
    --ink: #111111;
    --ink-soft: #333333;
    --rule: #555555;
    --night: #111111;
    --night-band: #1c1c1c;
    --night-light: #3a3a3a;
    --night-text: #ffffff;
  }
  * { margin: 0; padding: 0; box-sizing: border-box; }
  html, body { width: 1200px; height: 788px; overflow: hidden; }
  body {
    background: var(--stage);
    font-family: "Lato", sans-serif;
    color: var(--ink);
    position: relative;
  }
  .card {
    position: absolute;
    top: 239px;
    width: 540px;
    height: 310px;
    border-radius: 22px;
    overflow: hidden;
  }
  .card-front { left: 40px; background: var(--paper); }
  .card-back { left: 620px; background: var(--night); }

  .brand {
    position: absolute;
    left: 32px;
    top: 0;
    height: 310px;
    width: 196px;
    display: flex;
    flex-direction: column;
    justify-content: center;
  }
  .brand-name {
    font-weight: 900;
    font-size: 42px;
    line-height: 1;
    letter-spacing: -1px;
    color: var(--ink);
  }
  .divider {
    position: absolute;
    left: 238px;
    top: 56px;
    width: 1px;
    height: 198px;
    background: var(--rule);
  }
  .details {
    position: absolute;
    left: 258px;
    top: 42px;
    right: 14px;
  }
  .person-name {
    font-weight: 700;
    font-size: 28px;
    line-height: 1.1;
  }
  .person-title {
    font-weight: 300;
    font-size: 17px;
    color: var(--ink-soft);
    margin: 4px 0 14px;
  }
  .contact-list { list-style: none; }
  .contact-item {
    display: flex;
    align-items: center;
    gap: 8px;
    font-weight: 400;
    font-size: 17px;
    line-height: 1.6;
    white-space: nowrap;
  }
  .contact-item svg { width: 14px; height: 14px; flex: none; }
  .address {
    font-weight: 400;
    font-size: 17px;
    line-height: 1.4;
    margin-top: 8px;
  }

  .back-field {
    position: absolute;
    inset: 0;
    background:
      radial-gradient(ellipse at 85% 35%, rgba(90,90,90,0.45) 0%, rgba(90,90,90,0) 60%),
      linear-gradient(160deg, var(--night) 0%, var(--night-band) 35%, var(--night-light) 70%, var(--night-band) 100%);
  }
  .back-name {
    position: absolute;
    left: 0;
    right: 0;
    top: 140px;
    text-align: center;
    font-weight: 900;
    font-size: 32px;
    color: var(--night-text);
    letter-spacing: -0.5px;
  }
</style>
</head>
<body>
  <section class="card card-front">
    <div class="brand">
      <div class="brand-name">Veltrane Group</div>
    </div>
    <div class="divider"></div>
    <div class="details">
      <div class="person-name">Rohesh Kamdar</div>
      <div class="person-title">CEO</div>
      <ul class="contact-list">
        <li class="contact-item">
          <svg viewBox="0 0 14 14" aria-hidden="true"><rect x="3" y="1" width="8" height="12" rx="1.5" fill="none" stroke="#111" stroke-width="1.4"/><line x1="6" y1="11" x2="8" y2="11" stroke="#111" stroke-width="1.2"/></svg>
          <span>604.781.2249</span>
        </li>
        <li class="contact-item">
          <svg viewBox="0 0 14 14" aria-hidden="true"><rect x="1" y="3" width="12" height="9" fill="#111"/><polyline points="1,3 7,8 13,3" fill="none" stroke="#fff" stroke-width="1.2"/></svg>
          <span>roheshkamdar@veltrane.com</span>
        </li>
        <li class="contact-item">
          <svg viewBox="0 0 14 14" aria-hidden="true"><circle cx="7" cy="7" r="6" fill="#111"/><ellipse cx="7" cy="7" rx="2.5" ry="6" fill="none" stroke="#fff" stroke-width="0.9"/><line x1="1" y1="7" x2="13" y2="7" stroke="#fff" stroke-width="0.9"/></svg>
          <span>www.veltrane.com</span>
        </li>
      </ul>
      <div class="address">4180 Lindqvist Ave,<br>Tampa, FL 33482</div>
    </div>
  </section>

  <section class="card card-back">
    <div class="back-field" role="img" aria-label="Dark tone-on-tone repeating brand name pattern, fading lighter toward the upper right"></div>
    <div class="back-name">Veltrane</div>
  </section>
</body>
</html>
```